Business Card Re-Design/Update

We'd like to update out business cards. I've included our current "Style guide" which has the colour scheme of the organisation in it. I've also included the branding files with logos etc in them.

I've also included a copy of one of our existing cards so that you can see how ugly/dated they look. I'd like a fresh modern corporate look.

Target Market(s)

These are for our clients, potential clients, industry contacts - like all business cards

Contact Information for Business Card

Name
Position
Company Address - Level 1, 47 Fernby Street, Carlow Qld 4072
Direct Phone
mobile
Email
Website -www.korvalit.com.au
Logo

Colors

Designer to choose colors to be used in the design.

Requirements
Must have
• Main Logo
• Cards will need to be editable to be able to personalize them for each new employee.
Nice to have
• The MapOut, ShipWell, KeepSteady would be okay to have if they can be sensibly and professionally added to the look without detracting from the main imagery.
• Maybe they could go on the back of the card? will leave this to your creative discretion as to whether/where they fit.
Should not have
• Should not have decorative or script fonts

```html
<!DOCTYPE html>
<html lang="en">
<head>
<meta charset="utf-8">
<title>Korvalit business card</title>
<link rel="stylesheet" href="https://fonts.googleapis.com/css2?family=Open+Sans:wght@400;600;700&display=swap">
<style>
  :root {
    --brand-red: #d71920;
    --ink: #3a3a3a;
    --paper: #ffffff;
    --backdrop: #eeeeee;
    --rule: #cccccc;
  }
  * { box-sizing: border-box; margin: 0; padding: 0; }
  html, body { width: 1200px; height: 881px; overflow: hidden; }
  body {
    background: var(--backdrop);
    font-family: "Open Sans", Arial, sans-serif;
    position: relative;
  }
  .card {
    position: absolute;
    width: 540px;
    height: 300px;
    top: 290px;
    overflow: hidden;
    box-shadow: 0 2px 4px rgba(0,0,0,.18);
  }
  .card--front { left: 40px; background: var(--paper); color: var(--ink); }
  .card--back { left: 620px; background: var(--brand-red); color: var(--paper); }

  .brand { display: flex; align-items: center; gap: 10px; }
  .brand__square { width: 24px; height: 24px; background: var(--brand-red); }
  .brand__name { font-weight: 600; font-size: 36px; line-height: 1; letter-spacing: -0.5px; }

  .card--front .brand { position: absolute; left: 32px; top: 34px; }
  .card--front .brand__name { color: var(--ink); }

  .corner-block {
    position: absolute; right: 0; bottom: 0; width: 150px; height: 300px;
    background: var(--brand-red);
    clip-path: polygon(100% 0, 100% 100%, 0 100%, 0 68%);
  }

  .person { position: absolute; left: 90px; top: 112px; }
  .person__name { color: var(--brand-red); font-weight: 700; font-size: 20px; line-height: 1.2; }
  .person__title { font-size: 13px; margin-top: 1px; }
  .person__rule { width: 36px; height: 1px; background: var(--rule); margin: 8px 0 10px; }
  .person__address { font-size: 13px; margin-bottom: 10px; }
  .contacts { list-style: none; font-size: 12.5px; line-height: 17.5px; }
  .contacts li { display: flex; align-items: center; gap: 9px; }
  .contacts svg { width: 11px; height: 11px; fill: var(--brand-red); flex: none; }

  .card--back .brand { flex-direction: column; position: absolute; left: 0; right: 0; top: 60px; gap: 16px; }
  .card--back .brand__square { width: 44px; height: 44px; background: var(--paper); }
  .card--back .brand__name { font-size: 46px; color: var(--paper); }
  .services {
    position: absolute; left: 0; right: 0; bottom: 40px;
    display: flex; justify-content: center; gap: 28px;
    list-style: none; font-weight: 600; font-size: 14px;
  }
  .services li { display: flex; align-items: center; gap: 6px; }
  .services li::before { content: ""; width: 9px; height: 9px; border: 2px solid var(--paper); }
</style>
</head>
<body>
  <section class="card card--front" aria-label="Card front">
    <div class="brand">
      <span class="brand__square"></span>
      <span class="brand__name">korvalit</span>
    </div>
    <div class="person">
      <p class="person__name">Mara Ellison</p>
      <p class="person__title">Business Development Manager</p>
      <div class="person__rule"></div>
      <p class="person__address">Level 1, 47 Fernby Street, Carlow Qld 4072</p>
      <ul class="contacts">
        <li><svg viewBox="0 0 12 12"><path d="M3 0h6v12H3zM4 1.5v7.5h4V1.5z"/></svg>+61 (0)412 507 368</li>
        <li><svg viewBox="0 0 12 12"><path d="M2 0.5l2.2 0.3 0.8 2.8-1.4 1a7 7 0 0 0 3.8 3.8l1-1.4 2.8 0.8 0.3 2.2c-1 1.2-3 1.2-5 0S1.6 6.6 0.6 4.6 0.8 1.5 2 0.5z"/></svg>+61 (0)7 3180 4426</li>
        <li><svg viewBox="0 0 12 12"><path d="M0 2h12v1.2L6 7 0 3.2zM0 4.6l6 3.8 6-3.8V10H0z"/></svg>mellison@korvalit.com.au</li>
        <li><svg viewBox="0 0 12 12"><path d="M6 0a6 6 0 1 0 0 12A6 6 0 0 0 6 0zm0 1.3c.7.8 1.2 2 1.4 3.4H4.6C4.8 3.3 5.3 2.1 6 1.3zM1.4 5.9h2.1c0 1.3.3 2.5.8 3.5A4.7 4.7 0 0 1 1.4 5.9zm3.2 0h2.8c-.1 1.5-.6 2.8-1.4 3.8-.8-1-1.3-2.3-1.4-3.8zm3.9 0h2.1a4.7 4.7 0 0 1-2.9 3.5c.5-1 .8-2.2.8-3.5zm2.1-1.2H8.5c-.1-1.3-.4-2.4-.9-3.3a4.7 4.7 0 0 1 3 3.3zM4.4 1.4c-.5.9-.8 2-.9 3.3H1.4a4.7 4.7 0 0 1 3-3.3z"/></svg>www.korvalit.com.au</li>
      </ul>
    </div>
    <div class="corner-block" aria-hidden="true"></div>
  </section>

  <section class="card card--back" aria-label="Card back">
    <div class="brand">
      <span class="brand__square"></span>
      <span class="brand__name">korvalit</span>
    </div>
    <ul class="services">
      <li>MapOut</li>
      <li>KeepSteady</li>
      <li>ShipWell</li>
    </ul>
  </section>
</body>
</html>
```